I need a business card design for a new business based in South West Australia.
I specialize in residential window cleaning & general handyman maintenance.

Dale Marsh - 412 SILVER HAWK DETAILING
- Window Cleaning
- House Maintenance

```html
<!DOCTYPE html>
<html lang="en">
<head>
<meta charset="utf-8">
<title>412 Silver Hawk Detailing – Business Card</title>
<link href="https://fonts.googleapis.com/css2?family=Arimo:wght@400;700&family=Tinos:wght@400;700&display=swap" rel="stylesheet">
<style>
  :root {
    --page-bg: #e9e6e1;
    --card-edge: #f2f2f2;
    --photo-sky: #2a3540;
    --photo-mid: #262d33;
    --photo-ground: #1c2420;
    --text-light: #ffffff;
    --text-soft: #e6e8ea;
  }
  * { margin: 0; padding: 0; box-sizing: border-box; }
  html, body {
    width: 1200px;
    height: 892px;
    overflow: hidden;
    background: var(--page-bg);
  }
  .canvas {
    position: relative;
    width: 1200px;
    height: 892px;
    display: flex;
    align-items: center;
    justify-content: center;
  }
  .card {
    position: relative;
    width: 1000px;
    height: 572px;
    border: 6px solid var(--card-edge);
    overflow: hidden;
    box-shadow: 0 8px 24px rgba(0,0,0,0.25);
  }
  .card-photo {
    position: absolute;
    inset: 0;
    background:
      radial-gradient(ellipse at 62% 55%, rgba(70,72,76,0.55) 0%, rgba(40,44,48,0) 55%),
      linear-gradient(180deg, var(--photo-sky) 0%, var(--photo-mid) 55%, var(--photo-ground) 100%);
  }
  .card-content {
    position: absolute;
    inset: 0;
    color: var(--text-light);
  }
  .company-name {
    position: absolute;
    left: 56px;
    top: 78px;
    font-family: "Arimo", Arial, sans-serif;
    font-weight: 400;
    font-size: 46px;
    letter-spacing: 0.5px;
  }
  .company-tagline {
    position: absolute;
    left: 56px;
    top: 134px;
    font-family: "Tinos", "Times New Roman", serif;
    font-size: 25px;
    color: var(--text-soft);
    letter-spacing: 0.3px;
  }
  .owner-name {
    position: absolute;
    left: 420px;
    top: 220px;
    font-family: "Tinos", "Times New Roman", serif;
    font-weight: 700;
    font-size: 58px;
  }
  .service-list {
    position: absolute;
    left: 360px;
    top: 320px;
    list-style: none;
    font-family: "Arimo", Arial, sans-serif;
    font-size: 36px;
  }
  .service-item {
    display: flex;
    align-items: center;
    gap: 22px;
    margin-bottom: 28px;
  }
  .service-item:nth-child(2) { margin-left: 18px; }
  .service-icon { width: 24px; height: 24px; flex: none; }
</style>
</head>
<body>
  <main class="canvas">
    <article class="card">
      <div class="card-photo" role="img" aria-label="Photograph of a two-storey house among tall trees at dusk"></div>
      <div class="card-content">
        <h1 class="company-name">412 SILVER HAWK DETAILING</h1>
        <p class="company-tagline">residential window cleaning &amp; general handyman maintenance</p>
        <h2 class="owner-name">Dale Marsh</h2>
        <ul class="service-list">
          <li class="service-item">
            <svg class="service-icon" viewBox="0 0 24 24" aria-hidden="true">
              <circle cx="12" cy="12" r="7" fill="none" stroke="#fff" stroke-width="2"/>
              <circle cx="12" cy="12" r="2.5" fill="#fff"/>
              <path d="M12 1v5M12 18v5M1 12h5M18 12h5" stroke="#fff" stroke-width="2"/>
            </svg>
            <span>Window Cleaning</span>
          </li>
          <li class="service-item">
            <svg class="service-icon" viewBox="0 0 24 24" aria-hidden="true">
              <circle cx="12" cy="12" r="7" fill="none" stroke="#fff" stroke-width="2"/>
              <circle cx="12" cy="12" r="2.5" fill="#fff"/>
              <path d="M12 1v5M12 18v5M1 12h5M18 12h5" stroke="#fff" stroke-width="2"/>
            </svg>
            <span>House Maintenance</span>
          </li>
        </ul>
      </div>
    </article>
  </main>
</body>
</html>
```